Larkfield Ridge Management

I need a professional website. My current website is larkfieldridgemanagement.com and I hate it. It was created with some AI tool very quickly because I needed a site up and running with no advanced notice. I’m open to all designs .. I trust you, the professionals will deliver the results I’m anxiously awaiting! :)

```html
<!DOCTYPE html>
<html lang="en">
<head>
<meta charset="utf-8">
<title>Larkfield Ridge Management</title>
<link href="https://fonts.googleapis.com/css2?family=Outfit:wght@600;700;800&family=Open+Sans:wght@400;600;700&display=swap" rel="stylesheet">
<style>
:root{
  --navy:#1c2a4f;
  --navy-deep:#15203f;
  --red:#c8202c;
  --red-dark:#a8141f;
  --white:#ffffff;
  --ink:#333a48;
  --pale:#e8ebf4;
  --field:#f7eef0;
}
*{margin:0;padding:0;box-sizing:border-box}
html,body{width:1200px;height:4508px;overflow:hidden;background:var(--white)}
body{position:relative;font-family:"Open Sans",Arial,sans-serif;color:var(--ink)}
.abs{position:absolute}
.head{font-family:"Outfit",Arial,sans-serif;font-weight:800;line-height:1.1}
.btn{position:absolute;display:flex;align-items:center;justify-content:center;font-family:"Outfit",Arial,sans-serif;font-weight:700;font-size:17px;color:var(--white);letter-spacing:.3px;height:48px}
.btn::after{content:"";position:absolute;right:-16px;top:0;width:0;height:0;border-top:24px solid transparent;border-bottom:24px solid transparent;border-left:16px solid var(--red)}
.btn-navy{background:var(--navy)}
.btn-red{background:var(--red)}
.btn-red::after{border-left-color:var(--navy)}
.btn-outline{border:2px solid var(--white)}
.btn-outline::after{border-left-color:var(--white)}

/* header */
.topline{left:0;top:0;width:1200px;height:5px;background:var(--red)}
.site-header{left:0;top:5px;width:1200px;height:105px;background:var(--white)}
.brand{left:145px;top:22px;display:flex;align-items:center;gap:10px;width:240px}
.brand-mark{width:34px;height:34px;background:var(--red);flex:none}
.brand-name{font-family:"Outfit",Arial,sans-serif;font-weight:700;font-size:19px;color:var(--navy);line-height:1.15}
.nav{left:432px;top:48px;display:flex;gap:35px;font-family:"Open Sans",Arial,sans-serif;font-weight:700;font-size:16px;color:var(--navy)}
.nav .active{border-bottom:2px solid var(--red);padding-bottom:2px}
.login{left:918px;top:40px;width:118px;height:40px;background:var(--navy);color:var(--white);font-weight:700;font-size:14px;display:flex;align-items:center;justify-content:center;gap:8px}
.login::after{content:"";position:absolute;right:-14px;top:0;border-top:20px solid transparent;border-bottom:20px solid transparent;border-left:14px solid var(--red)}

/* hero */
.hero{left:0;top:110px;width:1200px;height:790px;background:linear-gradient(180deg,#2c3a60 0%,#3b4a6e 45%,#6d7688 75%,#8a8f97 100%)}
.hero-title{left:0;top:290px;width:1200px;text-align:center;color:var(--white);font-size:66px}
.hero-rule{left:265px;top:362px;width:670px;height:4px;background:var(--red)}

/* about */
.sec-title{font-size:54px;color:var(--navy)}
.sec-title span{color:var(--red)}
.rule{height:3px;width:130px;background:var(--red)}
.copy{font-size:16.5px;line-height:31px;text-align:justify;color:#4a505c}

/* services */
.card{position:absolute;top:2020px;width:324px;height:368px}
.card-body{position:absolute;left:0;top:125px;width:324px;text-align:center}
.card-title{font-family:"Open Sans",Arial,sans-serif;font-weight:700;font-size:15px;color:#1e2230;margin-bottom:18px}
.card-text{font-size:14px;line-height:24px;color:#4a505c;padding:0 50px}
.card.featured .card-title,.card.featured .card-text{color:var(--white)}

/* proposal */
.field{position:absolute;background:var(--field);border:1px solid #e2cfd3;font-size:15px;color:#333;padding:16px 20px}

/* footer */
.foot-h{font-family:"Outfit",Arial,sans-serif;font-weight:700;font-size:22px;color:var(--white)}
.foot-list{font-size:15px;color:var(--white);line-height:27px;list-style:none}
.contact-row{display:flex;align-items:center;gap:14px;font-size:15px;color:var(--white);height:34px;margin-bottom:14px}
.contact-ic{width:34px;height:34px;flex:none}
.social{display:flex;gap:8px}
.social span{width:32px;height:32px;border-radius:50%;border:2px solid var(--white);display:block}
.bottom-bar{left:0;top:4452px;width:1200px;height:56px}
.bottom-text{left:0;top:4470px;width:1200px;text-align:center;font-size:14px;color:var(--white)}
</style>
</head>
<body>

<div class="abs topline"></div>
<header class="abs site-header">
  <div class="abs brand"><span class="brand-mark"></span><span class="brand-name">Larkfield Ridge Management</span></div>
  <nav class="abs nav"><span class="active">HOME</span><span>SERVICES</span><span>ABOUT</span><span>NEWS</span><span>CONTACT</span></nav>
  <div class="abs login">
    <svg width="12" height="13" viewBox="0 0 12 13"><circle cx="6" cy="3.5" r="3" fill="#fff"/><path d="M0 13c0-4 2.5-5.5 6-5.5s6 1.5 6 5.5z" fill="#fff"/></svg>LOGIN</div>
</header>

<section class="abs hero" role="img" aria-label="Aerial view of a new residential neighbourhood of houses"></section>
<h1 class="abs head hero-title">A TRUE PARTNER,<br>NOT JUST A VENDOR.</h1>
<div class="abs hero-rule"></div>
<a class="btn btn-outline" style="left:378px;top:508px;width:180px;background:transparent">GET A QUOTE</a>
<a class="btn btn-red" style="left:611px;top:508px;width:180px">LEARN MORE</a>

<svg class="abs" style="left:0;top:740px" width="1200" height="170" viewBox="0 0 1200 170">
  <polygon points="0,160 275,8 372,62 828,62 880,65 1200,160 1200,170 0,170" fill="#fff"/>
  <polygon points="372,23 822,23 600,157" fill="#c8202c"/>
  <rect x="590" y="50" width="20" height="36" rx="10" fill="none" stroke="#fff" stroke-width="2"/>
  <path d="M592 92l8 7 8-7M592 101l8 7 8-7" fill="none" stroke="#fff" stroke-width="2"/>
</svg>

<!-- about -->
<h2 class="abs head sec-title" style="left:145px;top:920px">ABOUT <span>US</span></h2>
<div class="abs rule" style="left:145px;top:1000px"></div>
<p class="abs copy" style="left:145px;top:1028px;width:382px">Our organization delivers comprehensive property management solutions that optimize asset performance and tenant satisfaction. By integrating advanced analytics with proven operational frameworks, our specialists ensure each property achieves sustained value appreciation.Drawing on decades of collective expertise, the team facilitates regulatory compliance, cost efficiency, and proactive maintenance.</p>
<a class="btn btn-navy" style="left:145px;top:1337px;width:140px">READ MORE</a>
<a class="btn btn-red" style="left:312px;top:1337px;width:180px">REQUEST A QUOTE</a>

<svg class="abs" style="left:630px;top:800px" width="500" height="610" viewBox="0 0 500 610">
  <defs><linearGradient id="aboutPhoto" x1="0" y1="0" x2="1" y2="1"><stop offset="0" stop-color="#5b4a3d"/><stop offset="1" stop-color="#2a2320"/></linearGradient></defs>
  <polygon points="250,5 310,45 310,38 330,38 330,60 496,160 496,455 250,605 4,455 4,160" fill="none" stroke="#1c2a4f" stroke-width="5"/>
  <polygon role="img" aria-label="Hands stacking wooden blocks shaped like a house" points="250,40 478,172 478,445 250,580 22,445 22,172" fill="url(#aboutPhoto)"/>
  <polyline points="40,190 250,50 460,190" fill="none" stroke="#c8202c" stroke-width="14"/>
  <polygon points="190,490 310,490 250,525" fill="#c8202c"/>
</svg>

<!-- divider -->
<svg class="abs" style="left:0;top:1490px" width="1200" height="170" viewBox="0 0 1200 170">
  <polyline points="0,155 275,5 600,155 875,5 1200,155" fill="none" stroke="#e8ebf4" stroke-width="8"/>
</svg>

<!-- services -->
<h2 class="abs head sec-title" style="left:145px;top:1722px">OUR <span>SERVICES</span></h2>
<div class="abs rule" style="left:145px;top:1797px"></div>
<p class="abs copy" style="left:619px;top:1725px;width:438px">Our analysis demonstrates that effective property oversight originates from meticulous operational planning, transparent communication channels, and data-driven performance metrics across every asset class.By integrating advanced technology with industry expertise, our team implements proactive maintenance schedules that preserve asset value and facilitate sustainable, long-term returns for stakeholders.</p>

<div class="card" style="left:-78px">
  <svg class="abs" width="324" height="368" viewBox="0 0 324 368"><polygon points="162,4 320,95 320,275 162,364 4,275 4,95" fill="#fff" stroke="#e3e7f2" stroke-width="4"/>
  <circle cx="162" cy="80" r="22" fill="none" stroke="#c8202c" stroke-width="3"/><circle cx="162" cy="324" r="9" fill="none" stroke="#333" stroke-width="1.5"/></svg>
  <div class="card-body"><div class="card-title">BASIC SERVICE</div><div class="card-text">Sed ut perspiciatis unde omnis natuccusantium doloremque eSedciatis unde omnis natum accusantium doloremq</div></div>
</div>
<div class="card featured" style="left:265px">
  <svg class="abs" width="324" height="380" viewBox="0 0 324 380"><ellipse cx="162" cy="390" rx="90" ry="8" fill="#ddd"/><polygon points="162,2 322,94 322,276 162,366 2,276 2,94" fill="#c8202c"/><polygon points="162,16 310,101 310,269 162,352 14,269 14,101" fill="#1c2a4f"/>
  <circle cx="162" cy="80" r="22" fill="none" stroke="#fff" stroke-width="3"/><circle cx="162" cy="324" r="9" fill="none" stroke="#fff" stroke-width="1.5"/></svg>
  <div class="card-body"><div class="card-title">INTERMEDIATE SERVICE</div><div class="card-text">Sed ut perspiciatis unde omnis natuccusantium doloremque eSedciatis unde omnis natum accusantium doloremq</div></div>
</div>
<div class="card" style="left:610px">
  <svg class="abs" width="324" height="368" viewBox="0 0 324 368"><polygon points="162,4 320,95 320,275 162,364 4,275 4,95" fill="#fff" stroke="#e3e7f2" stroke-width="4"/>
  <circle cx="162" cy="80" r="22" fill="none" stroke="#c8202c" stroke-width="3"/><circle cx="162" cy="324" r="9" fill="none" stroke="#333" stroke-width="1.5"/></svg>
  <div class="card-body"><div class="card-title">ADVANCED SERVICE</div><div class="card-text">Sed ut perspiciatis unde omnis natuccusantium doloremque eSedciatis unde omnis natum accusantium doloremq</div></div>
</div>
<div class="card" style="left:954px">
  <svg class="abs" width="324" height="368" viewBox="0 0 324 368"><polygon points="162,4 320,95 320,275 162,364 4,275 4,95" fill="#fff" stroke="#e3e7f2" stroke-width="4"/>
  <circle cx="162" cy="80" r="22" fill="none" stroke="#c8202c" stroke-width="3"/><circle cx="162" cy="324" r="9" fill="none" stroke="#333" stroke-width="1.5"/></svg>
  <div class="card-body"><div class="card-title">ADVANCED + SERVICE</div><div class="card-text">Sed ut perspiciatis unde omnis natuccusantium doloremque eSedciatis unde omnis natum accusantium doloremq</div></div>
</div>

<!-- expertise -->
<svg class="abs" style="left:30px;top:2525px" width="500" height="600" viewBox="0 0 500 600">
  <defs>
    <linearGradient id="shake" x1="0" y1="0" x2="1" y2="1"><stop offset="0" stop-color="#c9b8a8"/><stop offset=".6" stop-color="#7d6f66"/><stop offset="1" stop-color="#2b2b30"/></linearGradient>
    <linearGradient id="office" x1="0" y1="0" x2="1" y2="1"><stop offset="0" stop-color="#e6e7ea"/><stop offset="1" stop-color="#8a8f99"/></linearGradient>
  </defs>
  <polygon points="220,2 430,122 430,370 220,490 8,370 8,122" fill="#fff" stroke="#c8202c" stroke-width="5"/>
  <polygon role="img" aria-label="Business handshake over a small model house" points="220,22 412,132 412,360 220,470 26,360 26,132" fill="url(#shake)"/>
  <polygon points="382,305 494,370 494,535 382,598 240,535 240,370" fill="#fff" stroke="#1c2a4f" stroke-width="5"/>
  <polygon role="img" aria-label="Smiling professional working at an office desk" points="382,322 480,380 480,525 382,582 254,525 254,380" fill="url(#office)"/>
</svg>
<h2 class="abs head" style="left:588px;top:2592px;font-size:54px;color:var(--navy);line-height:65px">EXPERTISE<br><span style="color:var(--red)">ROOTED IN ASSET</span><br>PRESERVATION</h2>
<div class="abs rule" style="left:588px;top:2804px;width:80px"></div>
<p class="abs copy" style="left:588px;top:2836px;width:460px;font-size:20px;line-height:31px">The organization applies rigorously tested frameworks and data-driven methodologies to safeguard property value while elevating tenant experience.</p>
<a class="btn btn-navy" style="left:588px;top:2995px;width:140px">READ MORE</a>

<!-- proposal -->
<svg class="abs" style="left:0;top:3195px" width="1200" height="1313" viewBox="0 0 1200 1313">
  <defs><linearGradient id="redfill" x1="0" y1="0" x2="0" y2="1"><stop offset="0" stop-color="#c8202c"/><stop offset=".6" stop-color="#b61b27"/><stop offset="1" stop-color="#9e1820"/></linearGradient></defs>
  <polygon points="0,550 143,470 143,0 0,0" fill="#fff"/>
  <rect x="0" y="550" width="1200" height="763" fill="#1c2a4f"/>
  <polygon points="0,550 143,470 1057,470 1200,550" fill="#1c2a4f"/>
  <polygon points="600,5 1057,205 1057,480 1200,560 1200,550 0,550 143,480 143,205" fill="#1c2a4f"/>
  <rect x="870" y="115" width="40" height="100" fill="#1c2a4f"/>
  <rect x="866" y="108" width="48" height="10" fill="#9aa0ad"/>
  <polygon points="600,38 1057,250 1057,760 600,970 143,760 143,250" fill="url(#redfill)" role="img" aria-label="Red-tinted view of suburban homes"/>
</svg>
<h2 class="abs head" style="left:0;top:3400px;width:1200px;text-align:center;font-size:54px;line-height:65px;color:var(--white)">REQUEST A TAILORED<br>PROPOSAL</h2>
<div class="abs" style="left:535px;top:3549px;width:130px;height:3px;background:var(--white)"></div>
<p class="abs" style="left:0;top:3580px;width:1200px;text-align:center;font-size:19px;line-height:31px;color:var(--white)">Submit the form to initiate a consultative assessment and explore<br>solutions aligned with your objectives.</p>
<div class="field" style="left:234px;top:3694px;width:359px;height:51px">First Name</div>
<div class="field" style="left:605px;top:3694px;width:359px;height:51px">Last Name</div>
<div class="field" style="left:234px;top:3759px;width:359px;height:51px">Email address</div>
<div class="field" style="left:605px;top:3759px;width:359px;height:51px">Phone Number</div>
<div class="field" style="left:234px;top:3824px;width:730px;height:113px">Message</div>
<a class="btn btn-navy" style="left:500px;top:3975px;width:185px">SUBMIT MESSAGE</a>
<style>.btn-navy.submit-fix::after{}</style>

<!-- footer -->
<div class="abs" style="left:145px;top:4228px">
  <div class="foot-h" style="margin-bottom:26px">CONTACT US</div>
  <div class="contact-row"><svg class="contact-ic" viewBox="0 0 34 34"><polygon points="17,1 31,9 31,25 17,33 3,25 3,9" fill="none" stroke="#fff" stroke-width="1.5"/><path d="M12 11c1 5 5 9 10 11l2-2-3-2-1 1c-2-1-4-3-5-5l1-1-2-3z" fill="#fff"/></svg>Call Us : +1 888 888 8888</div>
  <div class="contact-row" style="font-weight:700"><svg class="contact-ic" viewBox="0 0 34 34"><polygon points="17,1 31,9 31,25 17,33 3,25 3,9" fill="#c8202c"/><rect x="11" y="12" width="12" height="9" fill="#fff"/><path d="M11 12l6 5 6-5" fill="none" stroke="#c8202c" stroke-width="1.2"/></svg>info@larkfieldridgemanagement.com</div>
  <div class="contact-row"><svg class="contact-ic" viewBox="0 0 34 34"><polygon points="17,1 31,9 31,25 17,33 3,25 3,9" fill="none" stroke="#fff" stroke-width="1.5"/><path d="M17 10a5 5 0 0 0-5 5c0 4 5 9 5 9s5-5 5-9a5 5 0 0 0-5-5z" fill="#fff"/><circle cx="17" cy="15" r="2" fill="#1c2a4f"/></svg>123,Lorem ipsum dolore siu</div>
</div>
<div class="abs" style="left:530px;top:4228px">
  <div class="foot-h" style="margin-bottom:12px">MENUS</div>
  <ul class="foot-list"><li>Home</li><li>About us</li><li>Services</li><li>News</li><li>Contact Us</li></ul>
</div>
<div class="abs" style="left:705px;top:4228px">
  <div class="foot-h" style="margin-bottom:12px">LINKS</div>
  <ul class="foot-list"><li>Privacy Policy</li><li>Terms of use</li><li>Sitemap</li><li>Information</li></ul>
</div>
<div class="abs" style="left:887px;top:4228px">
  <div class="foot-h" style="margin-bottom:16px">SOCIAL MEDIA</div>
  <div class="social" aria-label="Social media links"><span></span><span></span><span></span><span></span></div>
</div>

<svg class="abs bottom-bar" width="1200" height="56" viewBox="0 0 1200 56"><polygon points="350,0 1200,0 1200,56 300,56" fill="#c8202c"/></svg>
<div class="abs bottom-text">© 2026 Companyname. All rights reserved &nbsp;|&nbsp; Privacy &nbsp;|&nbsp; Terms of Use</div>

</body>
</html>
```